Pyschiatry Experts need Marketing Campaign

Ad(s) developed for print advertising sharing our purpose and services, highlighting our medical care providers. Must be welcoming and inviting while displaying a high level of professionalism expected from a physician's office.

Target Market(s)

Local community

Industry/Entity Type

Psychiatry (Healthcare)

Requirements
Must have
• Staff pictures, 'Medication Management Experts', 'Prompt Appointments', 'ADD/ADHD, Bipolar Disorder, Depression, Anxiety, Schizophrenia, Grief Reaction and others' 'Virtual and In-Person Visits'
Nice to have
• Address: 412 E Marlowe Coeur d'Alene Phone (208)555-7193 website: BrightLoftCare.com Hours: Mon - Thur 7am - 6pm

```html
<!DOCTYPE html>
<html lang="en">
<head>
<meta charset="utf-8">
<title>Brightloft Health – Medication Management Experts</title>
<link rel="stylesheet" href="https://fonts.googleapis.com/css2?family=Playfair+Display:wght@700&family=Nunito+Sans:wght@400;600&display=swap">
<style>
  :root {
    --forest: #02604f;
    --teal: #139688;
    --brand-teal: #17a596;
    --lime: #a8e053;
    --tick: #8cd63c;
    --paper: #f8f8f6;
    --ink: #3b3d3d;
    --ink-dark: #1f3b35;
    --white: #ffffff;
  }
  * { margin: 0; padding: 0; box-sizing: border-box; }
  html, body { width: 921px; height: 1200px; overflow: hidden; }
  body { font-family: "Nunito Sans", Arial, sans-serif; color: var(--ink); }

  .flyer { position: relative; width: 921px; height: 1200px; background: var(--paper); overflow: hidden; }
  .panel-right { position: absolute; left: 482px; top: 0; right: 0; bottom: 0; background: var(--forest); }

  .brand { position: absolute; left: 57px; top: 62px; width: 353px; text-align: center; }
  .brand-dot { width: 96px; height: 96px; border-radius: 50%; background: var(--brand-teal); margin: 0 auto 22px; }
  .brand-name { font-family: "Playfair Display", Georgia, serif; font-weight: 700; color: var(--brand-teal); font-size: 38px; line-height: 1.05; letter-spacing: 1px; }

  .headline-bar { position: absolute; left: 470px; top: 88px; width: 19px; height: 176px; background: var(--lime); }
  .headline { position: absolute; left: 503px; top: 90px; font-family: "Playfair Display", Georgia, serif; font-weight: 700; color: var(--white); font-size: 54px; line-height: 58px; }

  .intro { position: absolute; left: 57px; top: 309px; width: 355px; font-size: 23px; line-height: 34px; }

  .services { position: absolute; left: 57px; top: 556px; list-style: none; }
  .services li { display: flex; align-items: center; height: 42.5px; font-size: 21.5px; }
  .services svg { width: 20px; height: 18px; margin-right: 15px; flex: none; }

  .provider { position: absolute; width: 216px; height: 296px; border: 3px solid var(--white); box-shadow: 0 4px 10px rgba(0,0,0,.35); }
  .provider .portrait { width: 100%; height: 100%; background: radial-gradient(circle at 50% 35%, #6f7d80 0%, #3a4548 55%, #1d2527 100%); }
  .provider .name { position: absolute; left: -3px; height: 29px; padding: 0 14px; background: var(--teal); color: var(--white); font-size: 16px; line-height: 29px; white-space: nowrap; }
  .p1 { left: 439px; top: 313px; } .p1 .name { bottom: 16px; width: 127px; }
  .p2 { left: 667px; top: 419px; } .p2 .name { bottom: 20px; width: 165px; }
  .p3 { left: 439px; top: 626px; } .p3 .name { bottom: 24px; width: 127px; }
  .p4 { left: 667px; top: 732px; } .p4 .name { bottom: 21px; width: 158px; }

  .contact { position: absolute; left: 56px; top: 948px; width: 591px; height: 195px; background: var(--teal); box-shadow: 0 6px 12px rgba(0,0,0,.25); }
  .contact-list { position: absolute; left: 44px; top: 28px; list-style: none; color: var(--white); font-size: 24px; line-height: 36.5px; }
  .contact-list li { display: flex; align-items: flex-start; }
  .contact-list svg { width: 24px; height: 24px; margin: 6px 16px 0 0; flex: none; fill: var(--white); }

  .hours { position: absolute; left: 455px; top: 946px; width: 166px; height: 156px; background: var(--lime); color: var(--ink-dark); padding: 36px 0 0 15px; }
  .hours-title { font-size: 25px; line-height: 30px; padding-bottom: 4px; border-bottom: 1.5px solid var(--white); display: inline-block; width: 68px; white-space: nowrap; }
  .hours-time { font-size: 23px; line-height: 27px; margin-top: 6px; }
</style>
</head>
<body>
<main class="flyer">
  <div class="panel-right"></div>

  <header class="brand">
    <div class="brand-dot"></div>
    <div class="brand-name">BRIGHTLOFT<br>HEALTH</div>
  </header>

  <div class="headline-bar"></div>
  <h1 class="headline">Medication<br>Management<br>Experts</h1>

  <p class="intro">Bringing comprehensive evaluation, medication management and psychotherapy to the full spectrum of mental health disorders including:</p>

  <ul class="services">
    <li><svg viewBox="0 0 20 18"><path d="M2 9 L8 15 L18 2" fill="none" stroke="#8cd63c" stroke-width="3.5" stroke-linecap="round" stroke-linejoin="round"/></svg>Prompt Appointments</li>
    <li><svg viewBox="0 0 20 18"><path d="M2 9 L8 15 L18 2" fill="none" stroke="#8cd63c" stroke-width="3.5" stroke-linecap="round" stroke-linejoin="round"/></svg>ADD/ADHD</li>
    <li><svg viewBox="0 0 20 18"><path d="M2 9 L8 15 L18 2" fill="none" stroke="#8cd63c" stroke-width="3.5" stroke-linecap="round" stroke-linejoin="round"/></svg>Bipolar Disorder</li>
    <li><svg viewBox="0 0 20 18"><path d="M2 9 L8 15 L18 2" fill="none" stroke="#8cd63c" stroke-width="3.5" stroke-linecap="round" stroke-linejoin="round"/></svg>Depression</li>
    <li><svg viewBox="0 0 20 18"><path d="M2 9 L8 15 L18 2" fill="none" stroke="#8cd63c" stroke-width="3.5" stroke-linecap="round" stroke-linejoin="round"/></svg>Anxiety</li>
    <li><svg viewBox="0 0 20 18"><path d="M2 9 L8 15 L18 2" fill="none" stroke="#8cd63c" stroke-width="3.5" stroke-linecap="round" stroke-linejoin="round"/></svg>Schizophrenia</li>
    <li><svg viewBox="0 0 20 18"><path d="M2 9 L8 15 L18 2" fill="none" stroke="#8cd63c" stroke-width="3.5" stroke-linecap="round" stroke-linejoin="round"/></svg>Grief Reaction and others</li>
    <li><svg viewBox="0 0 20 18"><path d="M2 9 L8 15 L18 2" fill="none" stroke="#8cd63c" stroke-width="3.5" stroke-linecap="round" stroke-linejoin="round"/></svg>Virtual and In-Person Visits</li>
  </ul>

  <figure class="provider p1">
    <div class="portrait" role="img" aria-label="Portrait photo of provider Mark Dellow"></div>
    <figcaption class="name">Mark Dellow</figcaption>
  </figure>
  <figure class="provider p2">
    <div class="portrait" role="img" aria-label="Portrait photo of provider Clara Whitfield"></div>
    <figcaption class="name">Clara Whitfield</figcaption>
  </figure>
  <figure class="provider p3">
    <div class="portrait" role="img" aria-label="Portrait photo of provider Dean Harlow"></div>
    <figcaption class="name">Dean Harlow</figcaption>
  </figure>
  <figure class="provider p4">
    <div class="portrait" role="img" aria-label="Portrait photo of provider Ruth Ambrose"></div>
    <figcaption class="name">Ruth Ambrose</figcaption>
  </figure>

  <section class="contact">
    <ul class="contact-list">
      <li><svg viewBox="0 0 24 24"><path d="M6.6 10.8a15.1 15.1 0 0 0 6.6 6.6l2.2-2.2c.3-.3.7-.4 1-.2 1.1.4 2.3.6 3.6.6.6 0 1 .4 1 1V20c0 .6-.4 1-1 1A17 17 0 0 1 3 4c0-.6.4-1 1-1h3.5c.6 0 1 .4 1 1 0 1.3.2 2.5.6 3.6.1.3 0 .7-.2 1z"/></svg>(208)555-7193</li>
      <li><svg viewBox="0 0 24 24"><path d="M3 4 L21 10 L13 12.5 L10 21 Z"/></svg>BrightLoftCare.com</li>
      <li><svg viewBox="0 0 24 24"><path d="M12 2a7 7 0 0 0-7 7c0 5.2 7 13 7 13s7-7.8 7-13a7 7 0 0 0-7-7zm0 9.5a2.5 2.5 0 1 1 0-5 2.5 2.5 0 0 1 0 5z"/></svg>412 E Marlowe Coeur<br>d'Alene</li>
    </ul>
  </section>

  <aside class="hours">
    <div class="hours-title">HOURS</div>
    <div class="hours-time">Mon - Thur<br>7am - 6pm</div>
  </aside>
</main>
</body>
</html>
```